we can communicate on this, but i want to follow the approach we took on Pellew|Marsh & Quinlan but i feel the card front needs the black background and the platinum and gold logo. The back? I am open. we can use the same info from PM&Q. Velmont Arc is an enhanced equity investment fund - basically a very exclusive boutique hedge fund that uses only stock options. very advanced things. hope you are interested

Contact Information for Business Card

Dr. Lewis T. Brennick, CFA
Scientifique de fusée financière
701.555.0143
LTBquant47@mailvantor.com

4718 Willow Creek Bend W.
West Fargo, ND 58078

No web site

Colors

Designer to choose colors to be used in the design.

Requirements
Nice to have
• I tend to prefer the most visible applications of the logo to include logo and name, the logo version with a black background and the gold and platinum components separated by the black. I see this working well for a single side (logo and name - this is card front to me).
• I am fairly open to other treatments on the reverse side with the data. To me, it makes sense to have a different color rendition of the logo on the reverse and it may be a muted black tone on tone or an oversized portion that would have spot UV. Or, the reverse may play with colors and layout
Should not have
• Other colors = no no
• Decorative font

```html
<!DOCTYPE html>
<html lang="en">
<head>
<meta charset="utf-8">
<title>Velmont Arc — Business Card</title>
<link rel="stylesheet" href="https://fonts.googleapis.com/css2?family=Montserrat:wght@700&family=Open+Sans:wght@600;700&family=Roboto:wght@400&display=swap">
<style>
  :root {
    --backdrop: #c8c8c8;
    --card-light: #ffffff;
    --card-dark: #151618;
    --gold: #d1ab4c;
    --ink: #1e1e20;
    --body-text: #4a4a4a;
    --on-dark: #ffffff;
  }
  * { box-sizing: border-box; margin: 0; padding: 0; }
  html, body {
    width: 1125px; height: 1200px; overflow: hidden;
    background: var(--backdrop);
  }
  .canvas { position: relative; width: 1125px; height: 1200px; }
  .card {
    position: absolute; left: 178px; width: 768px; height: 436px;
    border-radius: 24px; overflow: hidden;
  }
  .card--info { top: 140px; background: var(--card-light); }
  .card--brand { top: 626px; background: var(--card-dark); }

  .brand-mark { position: absolute; border-radius: 50%; background: var(--gold); }
  .brand-name {
    position: absolute; font-family: "Montserrat", sans-serif; font-weight: 700;
    white-space: nowrap; transform: translateX(-50%); line-height: 1;
  }
  .card--info .brand-mark { left: 160px; top: 143px; width: 90px; height: 90px; }
  .card--info .brand-name { left: 205px; top: 249px; font-size: 28px; color: var(--ink); letter-spacing: 0.5px; }

  .card--brand .brand-mark { left: 315px; top: 102px; width: 138px; height: 138px; }
  .card--brand .brand-name { left: 384px; top: 263px; font-size: 48px; color: var(--on-dark); letter-spacing: 1px; }

  .divider { position: absolute; left: 350px; top: 112px; width: 2px; height: 212px; background: var(--gold); }

  .person { position: absolute; left: 382px; top: 108px; width: 370px; }
  .person__name {
    font-family: "Open Sans", sans-serif; font-weight: 700; font-size: 20px;
    color: var(--gold); line-height: 28px; white-space: nowrap;
  }
  .person__role {
    font-family: "Open Sans", sans-serif; font-weight: 600; font-size: 17px;
    color: var(--ink); line-height: 26px; margin-top: 2px; white-space: nowrap;
  }
  .person__address {
    font-family: "Roboto", sans-serif; font-size: 16px; color: var(--body-text);
    line-height: 22px; margin-top: 10px;
  }
  .contact { list-style: none; margin-top: 14px; }
  .contact__item {
    display: flex; align-items: center; gap: 10px; height: 30px;
    font-family: "Roboto", sans-serif; font-size: 17px; color: var(--body-text);
    white-space: nowrap;
  }
  .contact__icon { width: 15px; height: 15px; flex: none; fill: var(--gold); }
</style>
</head>
<body>
<main class="canvas">
  <section class="card card--info" aria-label="Card with contact details">
    <div class="brand-mark"></div>
    <div class="brand-name">VELMONT ARC</div>
    <div class="divider"></div>
    <div class="person">
      <h1 class="person__name">DR. LEWIS T. BRENNICK, CFA</h1>
      <p class="person__role">Scientifique de fusée financière</p>
      <p class="person__address">4718 Willow Creek Bend W.<br>West Fargo, ND 58078</p>
      <ul class="contact">
        <li class="contact__item">
          <svg class="contact__icon" viewBox="0 0 16 16" aria-hidden="true"><path d="M3.5 1.5l2.3 2.6-1.2 1.8c.8 1.9 2.1 3.3 4 4.2l1.8-1.2 2.6 2.3-1.4 2.3C6.8 13.2 2.6 8.9 1.2 3z"/></svg>
          <span>701.555.0143</span>
        </li>
        <li class="contact__item">
          <svg class="contact__icon" viewBox="0 0 16 16" aria-hidden="true"><path d="M1 3h14v10H1zm1.5 1.5v.3L8 9l5.5-4.2v-.3z"/></svg>
          <span>LTBquant47@mailvantor.com</span>
        </li>
      </ul>
    </div>
  </section>

  <section class="card card--brand" aria-label="Brand card">
    <div class="brand-mark"></div>
    <div class="brand-name">VELMONT ARC</div>
  </section>
</main>
</body>
</html>
```